Luxury Wine Label for New Startup Winery

We need a wine label for our new winery startup. We have worked with a local designer but do not feel the resulting label / logo have the elevation required to present our brand as a luxury wine. Our winery is called "Quailbrook Vineyards" and we are focused on extremely high quality hand crafted artisan and estate wines from the Pacific Northwest.
We would like to see designs that utilize a tree line, or other imagery that represents the "Quailbrook" part of our company name. Another interesting feature could be wood grain.
A logo will be required based on your design so please design with this in mind:
This logo should be consistent with the wine bottle label design, and should be representative of our high end exclusive wine while giving a sense of place (Oregon/ Pacific Northwest.)
I will supply an image of the design we received from our local designer, PLEASE NOTE: in general we do like wood grain and tree line concepts but feel the execution was poorly done.
ATTN: Logo design should be suitable for use on: Bottles (Red wine/rose/white wine), Bussiness cards, vehicle signage, business signage, etc
P.S.:
If you have a design that is not outside the box we are still interested in seeing it.
Label is for a burgundy style bottle with a label height of 3.5 - 4" and a width of 3.5-4"
any label <= 4"x4" and >=3.5"x3.5" will be acceptable:
HOWEVER Width should be greater than or equal to height due to the bottle format
Target Market(s)
Wine enthusiasts with adequate discretionary budgets to afford $100 bottles of wine.
Industry/Entity Type
Wine / Winery
Requirements
Must have
- A sense of luxury, a feel of exclusivity, and a theme consistent with our product and brand name
Nice to have
- Tree line, wood grain or other wood themes. Serif fonts
Should not have
- anything cheesy, off topic, hard to read script fonts or anything that makes the label hard to read from a few feet away or too busy

```html
<!DOCTYPE html>
<html lang="en">
<head>
<meta charset="utf-8">
<title>Quailbrook Vineyards – Syrah Label</title>
<link rel="stylesheet" href="https://fonts.googleapis.com/css2?family=Cinzel:wght@600&family=Yellowtail&family=Questrial&display=block">
<style>
  :root {
    --page: #ffffff;
    --wood-dark: #8a2612;
    --wood-mid: #b23a1d;
    --wood-light: #c64a26;
    --panel-edge: #1e0006;
    --panel-deep: #33000a;
    --panel-glow: #6c0b17;
    --tree-shade: rgba(58, 4, 12, 0.75);
    --gold: #c8ab78;
    --gold-shadow: #2a0208;
  }

  * { margin: 0; padding: 0; box-sizing: border-box; }

  html, body {
    width: 1200px;
    height: 865px;
    overflow: hidden;
    background: var(--page);
  }

  .canvas {
    position: relative;
    width: 1200px;
    height: 865px;
  }

  .wine-label {
    position: absolute;
    left: 225px;
    top: 57px;
    width: 750px;
    height: 750px;
  }

  .wood-surround {
    position: absolute;
    inset: 0;
    background: linear-gradient(90deg,
      var(--wood-dark) 0%, var(--wood-mid) 30%, var(--wood-light) 50%,
      var(--wood-mid) 70%, var(--wood-dark) 100%);
    border: 1px solid var(--wood-dark);
  }

  .label-panel {
    position: absolute;
    left: 38px;
    top: 37px;
    width: 674px;
    height: 672px;
    background: radial-gradient(ellipse 70% 60% at 50% 52%,
      var(--panel-glow) 0%, var(--panel-deep) 70%, var(--panel-edge) 100%);
    box-shadow: 0 2px 6px rgba(0,0,0,0.5);
    overflow: hidden;
  }

  .gold-frame {
    position: absolute;
    inset: 10px;
    border: 5px solid var(--gold);
    z-index: 3;
  }

  .tree-line {
    position: absolute;
    left: 15px;
    right: 15px;
    top: 370px;
    height: 220px;
    background: linear-gradient(180deg,
      rgba(58,4,12,0) 0%, var(--tree-shade) 45%, rgba(50,3,10,0.55) 100%);
    z-index: 1;
  }

  .brand-mark {
    position: absolute;
    left: 50%;
    top: 42px;
    width: 106px;
    height: 106px;
    margin-left: -53px;
    border-radius: 50%;
    background: var(--gold);
    z-index: 2;
  }

  .brand-name {
    position: absolute;
    left: 0;
    right: 0;
    text-align: center;
    font-family: "Cinzel", serif;
    font-weight: 600;
    color: var(--gold);
    line-height: 1;
    z-index: 2;
  }

  .brand-name--primary {
    top: 157px;
    font-size: 42px;
    letter-spacing: 0.5px;
  }

  .brand-name--secondary {
    top: 200px;
    font-size: 26px;
    display: flex;
    align-items: center;
    justify-content: center;
    gap: 8px;
  }

  .brand-name--secondary::before,
  .brand-name--secondary::after {
    content: "";
    width: 40px;
    height: 2px;
    background: var(--gold);
  }

  .varietal {
    position: absolute;
    left: 0;
    right: 0;
    top: 258px;
    text-align: center;
    font-family: "Yellowtail", "Kaushan Script", cursive;
    font-weight: 400;
    font-size: 176px;
    line-height: 1.1;
    color: var(--gold);
    text-shadow: 4px 4px 0 var(--gold-shadow);
    z-index: 2;
  }

  .vintage-info {
    position: absolute;
    left: 0;
    right: 0;
    top: 522px;
    text-align: center;
    font-family: "Questrial", sans-serif;
    color: var(--gold);
    z-index: 2;
  }

  .vintage {
    display: block;
    font-size: 34px;
    letter-spacing: 2px;
    line-height: 42px;
  }

  .appellation {
    display: block;
    font-size: 22px;
    letter-spacing: 1.5px;
    line-height: 25px;
  }
</style>
</head>
<body>
  <main class="canvas">
    <section class="wine-label">
      <div class="wood-surround" role="img" aria-label="Red wood grain texture surrounding the label"></div>
      <div class="label-panel">
        <div class="tree-line" role="img" aria-label="Silhouetted pine tree line across the lower label"></div>
        <div class="brand-mark"></div>
        <p class="brand-name brand-name--primary">QUAILBROOK</p>
        <p class="brand-name brand-name--secondary">VINEYARDS</p>
        <h1 class="varietal">Syrah</h1>
        <p class="vintage-info">
          <span class="vintage">2024</span>
          <span class="appellation">WILLAMETTE</span>
          <span class="appellation">VALLEY</span>
        </p>
        <div class="gold-frame"></div>
      </div>
    </section>
  </main>
</body>
</html>
```